Clear Plastic Card Design

I am looking to have a business card designed from my logo icon. I am looking to match the style of a different business card I have attached in the files.
Looking for a card that is plastic, with layers of transparency in the shape of my logo icon (also attached in the files) - not a circle like the other card. The winning design will incorporate the red icon logo on the front and back and include the charity's name, "Light for the Weary Souls" in the same or similar font, as well as an email and phone number. For now, use the email: email@lightfortheweary-mail.org and the phone number 555-382-7194.
We like how the sample business card has transparency, partial and full opacity layers and a matching color scheme. Files will need to be in vector so that our business card printing company can work with it.
UPDATE:
We've some excellent designs in, thank you everyone! I got an early review from the owner, and he requested a minor redirect to find his perfect design. He wants the design to stand out by NOT being a rectangle. Try instead a circle, square, or best yet - something that falls in the outline of the logo icon, either fully or partially. Thank you, everyone!
Light for the Weary Souls text should be incorporated as well as a phone and email.

```html
<!DOCTYPE html>
<html lang="en">
<head>
<meta charset="UTF-8">
<title>Light for the Weary Souls – Business Card</title>
<link href="https://fonts.googleapis.com/css2?family=Poppins:ital,wght@0,500;0,600;0,700;1,400&display=swap" rel="stylesheet">
<style>
  :root {
    --page-bg: #e8e4e4;
    --card-bg: #f8f5f5;
    --brand-red: #c8101a;
    --brand-deep: #b8000f;
    --brand-orange: #f26a12;
    --ink: #3a3a3a;
    --ink-soft: #444444;
    --white: #ffffff;
  }
  * { margin: 0; padding: 0; box-sizing: border-box; }
  html, body {
    width: 1200px;
    height: 900px;
    overflow: hidden;
    background: var(--page-bg);
    font-family: "Poppins", sans-serif;
  }
  .business-card {
    position: absolute;
    left: 120px;
    top: 154px;
    width: 960px;
    height: 592px;
    background: var(--card-bg);
    overflow: hidden;
    box-shadow: 0 10px 30px rgba(0,0,0,0.12);
  }
  .org-name {
    position: absolute;
    left: 54px;
    top: 58px;
    font-weight: 700;
    font-size: 50px;
    line-height: 61px;
    color: var(--brand-red);
    text-transform: uppercase;
    letter-spacing: -0.5px;
  }
  .brand-mark {
    position: absolute;
    left: 560px;
    top: 110px;
    width: 360px;
    display: flex;
    align-items: center;
    gap: 18px;
  }
  .brand-mark-dot {
    flex: 0 0 56px;
    height: 56px;
    border-radius: 50%;
    background: var(--brand-red);
  }
  .brand-mark-name {
    font-weight: 700;
    font-size: 44px;
    line-height: 52px;
    color: var(--brand-red);
  }
  .contact-phone {
    position: absolute;
    left: 52px;
    top: 384px;
    display: flex;
    align-items: center;
    gap: 16px;
  }
  .phone-icon { width: 50px; height: 50px; display: block; }
  .phone-number {
    font-weight: 600;
    font-size: 44px;
    color: var(--ink);
    letter-spacing: 1px;
  }
  .contact-email {
    position: absolute;
    left: 51px;
    top: 458px;
    font-style: italic;
    font-weight: 400;
    font-size: 28px;
    color: var(--ink-soft);
  }
  .card-band {
    position: absolute;
    left: 0;
    top: 0;
    width: 960px;
    height: 592px;
  }
</style>
</head>
<body>
  <div class="business-card">
    <svg class="card-band" viewBox="0 0 960 592" aria-hidden="true">
      <defs>
        <linearGradient id="bandGradient" x1="0" y1="0" x2="1" y2="0">
          <stop offset="0" stop-color="var(--brand-deep)"/>
          <stop offset="0.35" stop-color="#c8101a"/>
          <stop offset="0.53" stop-color="var(--brand-orange)"/>
          <stop offset="0.68" stop-color="#d61a14"/>
          <stop offset="1" stop-color="var(--brand-deep)"/>
        </linearGradient>
      </defs>
      <polygon points="0,548 619,548 620,576 735,478 960,478 960,592 0,592" fill="url(#bandGradient)"/>
      <polyline points="0,539 615,539 617,568 731,468 960,468" fill="none" stroke="var(--brand-red)" stroke-width="3"/>
    </svg>

    <h1 class="org-name">Light for the<br>Weary Souls</h1>

    <div class="brand-mark">
      <span class="brand-mark-dot"></span>
      <span class="brand-mark-name">Light for the Weary Souls</span>
    </div>

    <div class="contact-phone">
      <svg class="phone-icon" viewBox="0 0 50 50" aria-hidden="true">
        <circle cx="25" cy="25" r="25" fill="var(--brand-red)"/>
        <path d="M17 14c1.5-1 3-1 3.8.4l2.2 3.8c.6 1.1.3 2.2-.7 2.9l-1.6 1.1c1 2.6 3 4.7 5.4 6l1.2-1.5c.8-1 2-1.2 3-.5l3.6 2.4c1.3.9 1.2 2.4.1 3.8-1.6 2-4 2.8-6.6 1.8C20.6 31.8 15.6 26.5 14 20c-.6-2.4.9-4.8 3-6z" fill="var(--white)"/>
        <path d="M27 13.5a9 9 0 0 1 9 9M27 17.5a5 5 0 0 1 5 5" fill="none" stroke="var(--white)" stroke-width="2" stroke-linecap="round"/>
      </svg>
      <span class="phone-number">555-382-7194</span>
    </div>

    <p class="contact-email">email@lightfortheweary-mail.org</p>
  </div>
</body>
</html>
```